Cat-products company needs smart, yet endearing, business card

We need a business card design for a new, but up-and-running, business based in Honolulu, Hawaii. The business is Purrnest Nook Co. Our first product is the most environmentally-friendly cat grass kit ever seen on the planet. Future products, currently in the R&D phase, will include a variety of exciting cat scratchers. We also do consulting work to help apartment-dwellers make their home more cat-friendly and, in the future, plan on doing full, custom installs of structure to create high walkways for cats.

Target Market(s)

Middle-aged, apartment-dwelling, middle-class workers who own 1 or more cats and who dote on them.

Industry/Entity Type

Pet Care

Contact Information for Business Card

A striking, professional, yet warm and friendly design is what we're after.

Font styles to use
Serif
Sans Serif
Other font styles liked:
• Comfortaa

Colors

Designer to choose colors to be used in the design.

Requirements
Must have
• The company logo: (see attachment)
• The company name: Purrnest Nook Co
• The web address: www.purrnestnookco.com
• Email: support@purrnestnookco.com
• Phone: +1 (808) 571 6023
• Update (Fri Jun 30 3017 7:45pm Hawaii Time) I would like, is possible, uploaded picture of the cat grass kit on the back of the card with some text along the lines of: Purrnest Nook Co - Maker Of The Leafiest Feline Sprout Set Yet
Nice to have
• A cat picture, cartoon, real or silhouette that illustrates cats in action and/or relaxing; ie using the apartment space to live, play and relax in and being well-contented.
• Most of the website is done in the font: Comfortaa. It might be nice to continue using this for brand consistency.
Should not have
• Hard-to-read fonts.

```html
<!DOCTYPE html>
<html lang="en">
<head>
<meta charset="utf-8">
<title>Purrnest Nook Co – Business Card</title>
<link rel="stylesheet" href="https://fonts.googleapis.com/css2?family=Comfortaa:wght@400;700&display=swap">
<style>
  :root {
    --stage: #0d0d0d;
    --cream: #fbf7f2;
    --cocoa: #4b3029;
    --amber: #f6ad1c;
    --white: #ffffff;
    --grass-deep: #0f1a12;
    --grass: #2f5a32;
    --fur: #8a6a4a;
  }
  * { box-sizing: border-box; margin: 0; padding: 0; }
  html, body {
    width: 1200px; height: 1000px; overflow: hidden;
    background: var(--stage);
    font-family: 'Comfortaa', sans-serif;
  }
  .stage {
    position: relative; width: 1200px; height: 1000px;
    display: flex; justify-content: center; align-items: center; gap: 100px;
  }
  .card {
    position: relative; width: 380px; height: 640px; overflow: hidden;
    box-shadow: 0 12px 30px rgba(0,0,0,.6);
  }
  .card-front { background: var(--cream); }
  .card-front .shapes { position: absolute; inset: 0; }
  .brand {
    position: absolute; display: flex; align-items: center; gap: 12px;
  }
  .card-front .brand { top: 150px; left: 170px; }
  .brand-mark { width: 22px; height: 22px; border-radius: 50%; background: var(--cocoa); flex: none; }
  .brand-name {
    font-weight: 700; font-size: 26px; line-height: 1.05; color: var(--amber);
  }
  .details {
    position: absolute; left: 34px; bottom: 40px; color: var(--white);
  }
  .person-name { font-size: 24px; color: var(--amber); font-weight: 400; }
  .person-role { font-size: 15px; margin-top: 4px; margin-bottom: 16px; }
  .contact-list { list-style: none; font-size: 13px; }
  .contact-list li { display: flex; align-items: center; gap: 10px; margin-top: 7px; }
  .contact-list svg { width: 14px; height: 14px; flex: none; }

  .card-back { background: var(--grass-deep); }
  .cat-photo {
    position: absolute; inset: 0;
    background:
      radial-gradient(ellipse 60% 30% at 55% 25%, rgba(138,106,74,.85), transparent 70%),
      linear-gradient(180deg, #141414 0%, #1b2a1d 45%, var(--grass) 100%);
  }
  .card-back .brand { left: 150px; bottom: 70px; }
  .card-back .brand-mark { background: var(--white); width: 30px; height: 30px; border-radius: 4px; }
  .card-back .brand-name { color: var(--white); font-size: 34px; }
</style>
</head>
<body>
<main class="stage">
  <section class="card card-front" aria-label="Card front">
    <svg class="shapes" viewBox="0 0 380 640" width="380" height="640">
      <path d="M0 0 H150 C70 120 60 250 120 340 L0 420 Z" fill="var(--amber)"/>
      <path d="M178 0 C90 120 80 250 140 345" fill="none" stroke="var(--cocoa)" stroke-width="9"/>
      <path d="M0 420 C90 380 160 345 230 320 C290 300 340 285 380 270 V640 H0 Z" fill="var(--cocoa)"/>
    </svg>
    <div class="brand">
      <span class="brand-mark"></span>
      <span class="brand-name">Purrnest<br>Nook Co</span>
    </div>
    <div class="details">
      <p class="person-name">Leilani Moss</p>
      <p class="person-role">Manager</p>
      <ul class="contact-list">
        <li>
          <svg viewBox="0 0 14 14"><rect x="3" y="1" width="8" height="12" rx="1.5" fill="none" stroke="var(--amber)" stroke-width="1.4"/></svg>
          +1 (808) 571 6023
        </li>
        <li>
          <svg viewBox="0 0 14 14"><rect x="1" y="3" width="12" height="8" fill="var(--amber)"/><path d="M1 3 L7 8 L13 3" fill="none" stroke="var(--cocoa)" stroke-width="1.2"/></svg>
          support@purrnestnookco.com
        </li>
        <li>
          <svg viewBox="0 0 14 14"><circle cx="7" cy="7" r="6" fill="var(--amber)"/><path d="M1 7 H13 M7 1 C4 4 4 10 7 13 M7 1 C10 4 10 10 7 13" fill="none" stroke="var(--cocoa)" stroke-width="1"/></svg>
          www.purrnestnookco.com
        </li>
      </ul>
    </div>
  </section>

  <section class="card card-back" aria-label="Card back">
    <div class="cat-photo" role="img" aria-label="Photo of a tabby cat stepping through green grass"></div>
    <div class="brand">
      <span class="brand-mark"></span>
      <span class="brand-name">Purrnest<br>Nook Co</span>
    </div>
  </section>
</main>
</body>
</html>
```